Tea standup pouch labels

Dear designers,
I need a minimalistic and modern label for my loose tea stand-up pouches (100, 250 and 500gm packs). The label should cover 70-80% of the pouch face (front and rear both).
The label will be 2 part label - Front and Rear side labels.
The labels should have a green background (Pantone Green C) with Golden or White or black colour text. Please either use the Golden logo or black logo to see which looks good with Pantone Green C background.
I am also attaching the content file and a few other files (Assam tea logo) to be used in the label.
The Assam tea logo should be small at the bottom left or right side of the front side. The logo should be dominant on the front page (some of the designs I received have small logo and big "100% single estate tea" and "Assam logo" as big characters on the front page which is not what I am looking for.

The font style should note simple Times new roman or Arial. It should look modern and should be something matching to the logo sentence 'Freshest possible' but should also not be in italics. Please refer to files Font style reference front and back for the style of font. Also use the same box space design on the rear - Content should be in White background; the rectangular box edges should be rounded and the border should be in dual colour - Golden and white or in black and white depending on the logo colour used (golden or black).

For the Rear page - headings could be in Golden colour or black colour depending on the logo colour you choose to use and the text can be in white colour i.e. Option 1 - Headings in golden colour and text in white colour; Option 2 - Heading in Black colour and text in white colour or any other combination that looks good - designer to decide.

Please let me know if you need any further information.

thanks,
Rotek

33b8a4

```html
<!DOCTYPE html>
<html lang="en">
<head>
<meta charset="utf-8">
<title>Leafora – Pouch Labels</title>
<link href="https://fonts.googleapis.com/css2?family=Josefin+Sans:wght@300;400;600&family=Nunito+Sans:wght@400;600;700;800&display=swap" rel="stylesheet">
<style>
  :root{
    --stage:#ececea;
    --green-deep:#0b4f35;
    --green:#126b48;
    --green-light:#1f8a60;
    --gold:#ecd75c;
    --white:#ffffff;
    --ink:#1d1d1d;
    --rule:#9a9a9a;
  }
  *{box-sizing:border-box;margin:0;padding:0}
  html,body{width:1200px;height:910px;overflow:hidden;background:var(--stage)}
  body{font-family:"Nunito Sans",sans-serif;color:var(--white);position:relative}

  .label{
    position:absolute;top:170px;width:440px;height:590px;
    border-radius:42px 42px 8px 8px;
    background:
      radial-gradient(ellipse at 30% 20%, rgba(255,255,255,.10), transparent 55%),
      linear-gradient(160deg,var(--green-light) 0%,var(--green) 40%,var(--green-deep) 100%);
    overflow:hidden;
  }
  .label--front{left:120px}
  .label--rear{left:640px}

  /* Front */
  .brand{position:absolute;left:0;right:0;top:150px;text-align:center}
  .brand__dot{display:block;margin:0 auto 22px;width:70px;height:70px;border:3px solid var(--gold);border-radius:50%}
  .brand__name{font-family:"Josefin Sans",sans-serif;font-weight:300;font-size:66px;letter-spacing:10px;color:var(--gold);line-height:1}
  .tagline{position:absolute;left:110px;top:350px;width:220px;height:36px;border-radius:18px;
    background:linear-gradient(90deg,rgba(236,215,92,.15),rgba(236,215,92,.35),rgba(236,215,92,.15))}
  .front-footer{position:absolute;left:0;right:0;bottom:40px;display:flex;align-items:center;justify-content:center;gap:14px;
    color:var(--gold);font-weight:700;font-size:13.5px;line-height:1.25}
  .front-footer__claim{text-align:right}
  .front-footer__divider{width:1.5px;height:44px;background:var(--gold)}
  .front-footer__badge{width:66px;height:66px;border-radius:50%;background:var(--gold)}

  /* Rear */
  .rear-title{position:absolute;top:38px;left:0;right:0;text-align:center;font-family:"Josefin Sans",sans-serif;
    font-weight:600;font-size:18px;line-height:1.15;letter-spacing:.2px}
  .col{position:absolute;font-size:7.6px;line-height:1.38}
  .col--left{left:20px;top:92px;width:180px}
  .col--right{left:210px;top:92px;width:182px}
  .col p{margin-bottom:8px}
  .col h3{font-size:7.6px;font-weight:800;margin-top:6px}
  .col ul{list-style:none}
  .col li::before{content:"• "}

  .nutrition{background:var(--white);color:var(--ink);border:3px double var(--ink);padding:6px 7px;font-size:7px}
  .nutrition h2{font-size:16px;font-weight:800;border-bottom:2px solid var(--ink);padding-bottom:3px;margin-bottom:3px;letter-spacing:.2px}
  .nutrition table{width:100%;border-collapse:collapse}
  .nutrition th{font-weight:400;text-align:left;padding:2px 0;border-bottom:2px solid var(--ink);vertical-align:bottom}
  .nutrition th:last-child{text-align:right}
  .nutrition td{padding:1.5px 0;border-bottom:1px solid var(--rule)}
  .nutrition td:last-child{text-align:right}
  .nutrition .indent{padding-left:34px}
  .nutrition__note{margin-top:7px;font-size:7.3px;line-height:1.35}

  .contact{position:absolute;left:0;right:0;top:460px;text-align:center}
  .contact__web{font-size:12px;font-weight:700}
  .contact__mail{font-size:8px;font-weight:700;line-height:1.3}

  .sticker{position:absolute;top:500px;height:62px;border-radius:10px;background:var(--white)}
  .sticker--batch{left:32px;width:164px;color:var(--green);font-size:7px;line-height:1.35;text-align:center;padding-top:5px}
  .sticker--code{left:222px;width:164px}
</style>
</head>
<body>

<section class="label label--front" aria-label="Front label">
  <div class="brand">
    <span class="brand__dot"></span>
    <div class="brand__name">LEAFORA</div>
  </div>
  <div class="tagline" role="img" aria-label="Hand-lettered tagline: freshest possible"></div>
  <div class="front-footer">
    <div class="front-footer__claim">100% Single<br>Estate Tea</div>
    <span class="front-footer__divider"></span>
    <span class="front-footer__badge" aria-label="Origin certification badge"></span>
    <span class="front-footer__divider"></span>
    <div class="front-footer__weight">Net Wt<br>250g/8.82oz</div>
  </div>
</section>

<section class="label label--rear" aria-label="Rear label">
  <h1 class="rear-title">TEA LOSES ITS<br>FLAVOUR AND AROMA OVER TIME</h1>

  <div class="col col--left">
    <p>Tea tastes good for 24 months after being processed in the factory. Most tea that you get in stores passes through multiple middlemen (like auction house, wholesaler, local exporter etc) and takes between 6-12 months after harvest to reach you. By then tea has already lost a lot of its flavour and aroma.</p>
    <p>We come from a family of small-scale tea growers in Assam, India and will source tea directly from our own tea estates or from similar estates like us. Hence, we are able to tell you when the tea was picked from the garden and when it was packed. By sourcing tea directly from small-scale tea estates, we are removing middlemen, giving a better price to the tea growers and reducing the time it takes to reach tea lovers like yourself.</p>
    <h3>WHAT DOES IT TASTE LIKE?</h3>
    <ul><li>Strong, malty, astringent taste and aroma</li></ul>
    <h3>HOW DO I DRINK IT?</h3>
    <ul>
      <li>Rinse the teapot or cup with boiling water</li>
      <li>Add 2 teaspoon (~2 g) of tea leaves into the teapot and then pour boiling water and cover it with the lid</li>
      <li>Allow the tea to brew for one minute. Keep it longer for around three minutes for a stronger brew</li>
      <li>Pour the brew into a cup using a strainer</li>
      <li>Add milk and sugar to taste</li>
    </ul>
  </div>

  <div class="col col--right">
    <div class="nutrition">
      <h2>NUTRITIONAL FACTS</h2>
      <table>
        <tr><th>Typical Values</th><th>Per 100ml Brewed<br>Infusion*</th></tr>
        <tr><td>Energy</td><td>&lt;4 kcal</td></tr>
        <tr><td class="indent">Fat</td><td>0 g</td></tr>
        <tr><td>Of which saturates</td><td>0 g</td></tr>
        <tr><td class="indent">Carbohydrates</td><td>0 g</td></tr>
        <tr><td>Of which sugar</td><td>0 g</td></tr>
        <tr><td>Protein</td><td>&lt;0.5 g</td></tr>
        <tr><td>Salt</td><td>0 g</td></tr>
      </table>
      <p class="nutrition__note">*Based on an infusion brewed with 200ml water for 3 minutes.</p>
    </div>
    <h3>INGREDIENTS: BLACK TEA</h3>
    <p>Allergen information: Made in a factory that processes nuts.</p>
    <p><strong>HOW DO I STORE IT:</strong> Store in an airtight container made of ceramic or tin to keep the light out</p>
    <p style="font-weight:700">Packed in the UK<br>by Leafora Limited,<br>12 Alder Row, Reading, RG1 4QT,<br>United Kingdom</p>
  </div>

  <div class="contact">
    <div class="contact__web">Visit our website at www.leafora.co.uk</div>
    <div class="contact__mail">Write to us at hello@leafora.co.uk or Leafora Limited, 12 Alder Row,<br>Reading, RG1 4QT, United Kingdom</div>
  </div>

  <div class="sticker sticker--batch">
    "Blank space for sticker"<br>Picked on: September 2019<br>Packaged on: May 2020<br>Best before: May 2022<br>Tea type: Black Tea BOP<br>Batch no. LOT/12345ABC
  </div>
  <div class="sticker sticker--code"></div>
</section>

</body>
</html>
```